Email Preference Page Design

We are looking for a 2 page design for our users to edit their email preferences and submit friend referrals. You can find the fuctionality, content and text here:

https://brightvanta.mailrelayhub.example/app/linkClick/7281/5fa9c1d3b07e442b/28374615/9bd4e01a7c3f2a65

* the shipping and billing address might be different so you need to show the billing if the "same as shipping" box is not checked. It can auto-hide like the page above shows if that fits your design.

* when the "unsubscribe from all email lists" box is selected, all the other checkbox options will hide as in the example page. We need you to show us what the site will look like with and without that checkbox selected.

We want to match these two pages to the general feel of these website pages:

www.brightvanta.com
and
free.brightvanta.com

The page should be very clean and tight. Project is for design only but must be able to be implemented in html showing button and checkbox states. Technically this must be two pages for our system - one for all the user info and one for individual email referrals (see example above).

Target Market(s)

video professionals

Industry/Entity Type

Shipping

Requirements
Must have
• our logo (see numerous versions attached)
well designed header
well designed sections
clean editable text
tight layout
html friendly
easy to understand
2 pages
Nice to have
• custom checkboxes and radio buttons

```html
<!DOCTYPE html>
<html lang="en">
<head>
<meta charset="utf-8">
<title>Brightvanta – Communication Preferences</title>
<link href="https://fonts.googleapis.com/css2?family=Michroma&family=Open+Sans:wght@400;600&display=swap" rel="stylesheet">
<style>
  :root{
    --slate:#36474f;
    --field-border:#d4d8da;
    --field-text:#6d7478;
    --focus-bg:#f3fafd;
    --focus-border:#a6c3d1;
    --orange:#ff4a00;
    --gold:#e5aa2a;
    --white:#ffffff;
  }
  *{box-sizing:border-box;margin:0;padding:0}
  html,body{width:948px;height:1200px;overflow:hidden;background:var(--white)}
  body{position:relative;font-family:"Open Sans",sans-serif;color:var(--slate)}

  .hero{position:absolute;left:0;top:0;width:948px;height:318px;
    background:
      radial-gradient(ellipse 180px 120px at 90px 150px,rgba(230,60,80,.7),transparent),
      radial-gradient(ellipse 220px 90px at 520px 120px,rgba(40,190,230,.55),transparent),
      radial-gradient(ellipse 240px 140px at 820px 160px,rgba(230,90,150,.6),transparent),
      radial-gradient(ellipse 200px 100px at 380px 290px,rgba(240,200,60,.55),transparent),
      linear-gradient(180deg,#2a2440,#3b2a4a 60%,#4a3340);}
  .brand-tab{position:absolute;left:359px;top:0;width:230px;height:150px}
  .brand-name{position:absolute;left:359px;top:52px;width:230px;text-align:center;
    font-family:"Open Sans",sans-serif;font-weight:600;font-size:30px;color:var(--slate);letter-spacing:.5px}
  .page-title{position:absolute;left:0;top:172px;width:948px;text-align:center;
    font-family:"Michroma",sans-serif;font-size:37px;line-height:58px;color:var(--white);
    text-shadow:0 2px 4px rgba(0,0,0,.45)}

  .column{position:absolute;top:389px;width:403px}
  .column--contact{left:41px}
  .column--shipping{left:504px}

  .section-head{position:relative;height:53px;border-bottom:2px solid var(--slate)}
  .section-tab{position:absolute;left:0;top:0;height:53px}
  .section-title{position:absolute;left:19px;top:12px;font-size:22px;color:var(--white)}
  .required-note{position:absolute;right:0;bottom:4px;font-size:13px;color:var(--field-text)}

  .fields{display:flex;flex-direction:column}
  .column--contact .fields{margin-top:21px;gap:6px}
  .column--shipping .fields{margin-top:15px;gap:7px}
  .field{height:41px;border:1px solid var(--field-border);padding:0 11px;
    display:flex;align-items:center;font-size:16px;color:var(--field-text);position:relative;background:var(--white)}
  .field--active{background:var(--focus-bg);border-color:var(--focus-border)}
  .field--select::after{content:"";position:absolute;right:0;top:0;width:31px;height:39px;border-left:1px solid var(--field-border)}
  .field--select .caret{position:absolute;right:10px;top:16px}
  .postal-row{display:flex;align-items:center}
  .postal-row .field{width:180px}
  .postal-row .field:last-child{width:193px}
  .postal-plus{width:30px;text-align:center;font-size:14px;color:var(--field-text)}
  .postal-label{font-size:13px;color:var(--slate);margin-top:3px}

  .same-address{display:flex;align-items:flex-start;margin-top:24px;font-size:23px;line-height:28px}
  .checkbox{width:20px;height:20px;border:1px solid #b9bfc2;background:var(--white);flex:none}
  .same-address .checkbox{margin:6px 12px 0 0}

  .unsubscribe{margin-top:32px;height:50px;background:var(--gold);display:flex;align-items:center;
    padding-left:16px;font-size:23px;color:var(--white)}
  .unsubscribe .checkbox{width:19px;height:19px;border:2px solid var(--slate);margin-right:2px}

  .submit-button{position:absolute;left:41px;top:1038px;width:318px;height:65px;border-radius:33px;
    background:var(--orange);border:1px solid #d93e00;color:var(--white);font-size:30px;font-weight:600;
    display:flex;align-items:center;justify-content:center;text-shadow:0 1px 2px rgba(0,0,0,.35)}
</style>
</head>
<body>
  <header class="hero" role="img" aria-label="Blurred night-time photo of colourful neon city lights"></header>

  <svg class="brand-tab" viewBox="0 0 230 150" aria-hidden="true">
    <path d="M0 0H230V138Q115 160 0 138Z" fill="#1c1c1c"/>
    <path d="M0 0H230V132Q115 152 0 132Z" fill="#ffffff"/>
  </svg>
  <div class="brand-name">brightvanta</div>

  <h1 class="page-title">COMMUNICATION<br>PREFERENCES</h1>

  <section class="column column--contact">
    <div class="section-head">
      <svg class="section-tab" width="200" height="53" viewBox="0 0 200 53" aria-hidden="true"><path d="M0 0H164L200 53H0Z" fill="#36474f"/></svg>
      <span class="section-title">Contact Info</span>
      <span class="required-note">Required Fields*</span>
    </div>
    <div class="fields">
      <div class="field">First Name*</div>
      <div class="field field--active">Last Name*</div>
      <div class="field">Email *</div>
      <div class="field">Phone</div>
      <div class="field">Address 1</div>
      <div class="field">Address 2</div>
      <div class="field">Address 3</div>
      <div class="field">City</div>
      <div class="field field--select">Select Country
        <svg class="caret" width="11" height="8" viewBox="0 0 11 8" aria-hidden="true"><path d="M0 0H11L5.5 8Z" fill="#c2c7ca"/></svg></div>
      <div class="field">State</div>
      <div>
        <div class="postal-row">
          <div class="field">11111</div><span class="postal-plus">+</span><div class="field">1111</div>
        </div>
        <div class="postal-label">Postal Code + 4</div>
      </div>
    </div>
  </section>

  <section class="column column--shipping">
    <div class="section-head">
      <svg class="section-tab" width="200" height="53" viewBox="0 0 200 53" aria-hidden="true"><path d="M0 0H220L250 53H0Z" fill="#36474f"/></svg>
      <svg class="section-tab" width="250" height="53" viewBox="0 0 250 53" aria-hidden="true"><path d="M0 0H216L250 53H0Z" fill="#36474f"/></svg>
      <span class="section-title">Shipping Address</span>
      <span class="required-note">Required Fields*</span>
    </div>
    <label class="same-address"><span class="checkbox"></span><span>Billing address is same as<br>shipping address</span></label>
    <div class="fields">
      <div class="field">Street Address 1</div>
      <div class="field">Street Address 2</div>
      <div class="field">Street Address 3</div>
      <div class="field field--select">City
        <svg class="caret" width="11" height="8" viewBox="0 0 11 8" aria-hidden="true"><path d="M0 0H11L5.5 8Z" fill="#c2c7ca"/></svg></div>
      <div class="field">Select Country</div>
      <div class="field">State</div>
      <div>
        <div class="postal-row">
          <div class="field">44444</div><span class="postal-plus">+</span><div class="field">2222</div>
        </div>
        <div class="postal-label">Postal Code + 4</div>
      </div>
    </div>
    <label class="unsubscribe"><span class="checkbox"></span>Unsubscribe from all email lists</label>
  </section>

  <div class="submit-button">Submit Now</div>
</body>
</html>
```